Awesome business card design needed

We need a new business card design to go with our new logo.
We are a web development agency that specialises in highly complex back-end integrations as opposed to design, our customers are retailers, hotels, hospitals and any other organisation that has a large online marketing department.
Take a look at our website - www.brenoloft.com for some inspiration.
We want our new business cards to exude class, professionalism and style.
We are likely to choose a high-end card to print them on but we want the design of the card itself to really turn heads.
We have no specific colour requirements, the logo as you will see is a turquoise colour R89 G171 B167 #59aba7 but it can also be in white if you want to make the colour of the card something different.
The information on the card should be:
Name
Position
Tel
email
Potentially a double sided card could have our web address, twitter and FB links.

```html
<!DOCTYPE html>
<html lang="en">
<head>
<meta charset="utf-8">
<title>Brenoloft business card</title>
<link rel="stylesheet" href="https://fonts.googleapis.com/css2?family=Arvo:wght@400;700&display=swap">
<style>
  :root {
    --teal: #59aba7;
    --ink: #0c0c0c;
    --backdrop: #2a2a2a;
    --card-dark: #141414;
    --card-dark-soft: #3a3a3a;
  }
  * { margin: 0; padding: 0; box-sizing: border-box; }
  html, body { width: 1200px; height: 900px; overflow: hidden; }
  body {
    background: var(--backdrop);
    font-family: "Arvo", serif;
    position: relative;
  }
  .card {
    position: absolute;
    width: 500px;
    height: 286px;
    top: 307px;
    box-shadow: 0 10px 30px rgba(0,0,0,0.55);
    overflow: hidden;
  }
  .card-back {
    left: 70px;
    background: var(--card-dark);
  }
  .back-pattern {
    position: absolute;
    inset: 0;
    background: radial-gradient(ellipse at 45% 35%, var(--card-dark-soft), var(--card-dark) 75%);
    border: 10px solid var(--teal);
    border-style: dotted;
  }
  .back-name {
    position: absolute;
    inset: 0;
    display: flex;
    align-items: center;
    justify-content: center;
    font-size: 64px;
    font-weight: 700;
    color: #4a4a4a;
    letter-spacing: 1px;
  }
  .card-front {
    left: 630px;
    background: var(--teal);
    color: var(--ink);
  }
  .name-tab {
    position: absolute;
    left: 0;
    top: 100px;
    width: 186px;
    height: 52px;
    background: var(--ink);
    border-radius: 0 8px 8px 0;
    padding: 8px 0 0 22px;
    color: var(--teal);
  }
  .name-tab .person {
    font-size: 15px;
    letter-spacing: 0.5px;
    line-height: 1.1;
  }
  .name-tab .role {
    font-size: 12px;
    line-height: 1.3;
  }
  .wordmark {
    position: absolute;
    right: 34px;
    top: 78px;
    font-size: 44px;
    font-weight: 700;
    letter-spacing: 1px;
  }
  .contact {
    position: absolute;
    right: 26px;
    top: 166px;
    list-style: none;
  }
  .contact li {
    display: flex;
    justify-content: flex-end;
    align-items: center;
    gap: 8px;
    font-size: 13px;
    line-height: 20px;
  }
  .contact svg { width: 15px; height: 15px; flex: none; }
</style>
</head>
<body>
  <div class="card card-back">
    <div class="back-pattern" role="img" aria-label="Dark pixel-grid pattern with turquoise square border"></div>
    <div class="back-name">brenoloft</div>
  </div>

  <div class="card card-front">
    <div class="name-tab">
      <p class="person">MAREN TOLSEY</p>
      <p class="role">Customer Service</p>
    </div>
    <div class="wordmark">brenoloft</div>
    <ul class="contact">
      <li>555.014.2231
        <svg viewBox="0 0 16 16"><circle cx="8" cy="8" r="7" fill="none" stroke="currentColor" stroke-width="1"/><path d="M6 4.5c-1 1-1 3 .5 5s3.5 2.5 4.5 1.5l-1-1.2-1 .5c-.8-.4-1.8-1.4-2.2-2.2l.5-1z" fill="currentColor"/></svg>
      </li>
      <li>maren@brenoloft.com
        <svg viewBox="0 0 16 16"><circle cx="8" cy="8" r="7" fill="none" stroke="currentColor" stroke-width="1"/><rect x="4.5" y="5.5" width="7" height="5" fill="currentColor"/><path d="M4.5 5.5l3.5 3 3.5-3" fill="none" stroke="var(--teal)" stroke-width="0.8"/></svg>
      </li>
      <li>www.brenoloft.com
        <svg viewBox="0 0 16 16"><circle cx="8" cy="8" r="7" fill="none" stroke="currentColor" stroke-width="1"/></svg>
      </li>
      <li>friendhub.com/brenoloft
        <svg viewBox="0 0 16 16"><circle cx="8" cy="8" r="7" fill="none" stroke="currentColor" stroke-width="1"/></svg>
      </li>
      <li>@brenoloft
        <svg viewBox="0 0 16 16"><circle cx="8" cy="8" r="7" fill="none" stroke="currentColor" stroke-width="1"/></svg>
      </li>
    </ul>
  </div>
</body>
</html>
```